Luxury Wine Label for New Startup Winery

We need a wine label for our new winery startup. We have worked with a local designer but do not feel the resulting label / logo have the elevation required to present our brand as a luxury wine. Our winery is called "Quailbrook Vineyards" and we are focused on extremely high quality hand crafted artisan and estate wines from the Pacific Northwest.
We would like to see designs that utilize a tree line, or other imagery that represents the "Quailbrook" part of our company name. Another interesting feature could be wood grain.
A logo will be required based on your design so please design with this in mind:
This logo should be consistent with the wine bottle label design, and should be representative of our high end exclusive wine while giving a sense of place (Oregon/ Pacific Northwest.)
I will supply an image of the design we received from our local designer, PLEASE NOTE: in general we do like wood grain and tree line concepts but feel the execution was poorly done.
ATTN: Logo design should be suitable for use on: Bottles (Red wine/rose/white wine), Bussiness cards, vehicle signage, business signage, etc
P.S.:
If you have a design that is not outside the box we are still interested in seeing it.
Label is for a burgundy style bottle with a label height of 3.5 - 4" and a width of 3.5-4"
any label <= 4"x4" and >=3.5"x3.5" will be acceptable:
HOWEVER Width should be greater than or equal to height due to the bottle format
Target Market(s)
Wine enthusiasts with adequate discretionary budgets to afford $100 bottles of wine.
Industry/Entity Type
Wine / Winery
Requirements
Must have
- A sense of luxury, a feel of exclusivity, and a theme consistent with our product and brand name
Nice to have
- Tree line, wood grain or other wood themes. Serif fonts
Should not have
- anything cheesy, off topic, hard to read script fonts or anything that makes the label hard to read from a few feet away or too busy

```html
<!DOCTYPE html>
<html lang="en">
<head>
<meta charset="utf-8">
<title>Quailbrook Vineyards – Rosé Label</title>
<link rel="stylesheet" href="https://fonts.googleapis.com/css2?family=Cinzel:wght@400&family=Allura&family=Cormorant+Garamond:wght@500&display=swap">
<style>
  :root {
    --backdrop: #433c4d;
    --paper: #fbfafb;
    --blush: #f1cfe2;
    --blush-soft: #f6e3ee;
    --band-pink: #eec8dd;
    --ink: #1d1a1e;
    --gold: #b89257;
    --rule: #3a3538;
    --silver-dark: #1a1a1c;
    --silver-light: #d9d9dd;
  }
  * { box-sizing: border-box; margin: 0; padding: 0; }
  html, body {
    width: 1200px; height: 1200px; overflow: hidden;
    background: var(--backdrop);
  }
  .label {
    position: absolute; left: 100px; top: 110px;
    width: 1000px; height: 980px;
    background: var(--paper);
    box-shadow: 0 10px 40px rgba(0,0,0,0.35);
    overflow: hidden;
  }
  .label__field {
    position: absolute; left: 0; top: 0; width: 1000px; height: 673px;
    background:
      radial-gradient(ellipse at 20% 25%, var(--blush) 0%, transparent 35%),
      radial-gradient(ellipse at 85% 60%, var(--blush) 0%, transparent 40%),
      radial-gradient(ellipse at 40% 90%, var(--blush-soft) 0%, transparent 45%),
      var(--paper);
  }
  .label__rule {
    position: absolute; left: 0; width: 1000px; height: 1.5px;
    background: var(--rule);
  }
  .label__rule--top { top: 37px; }
  .label__rule--bottom { top: 659px; }
  .brand {
    position: absolute; left: 0; top: 228px; width: 1000px;
    display: flex; flex-direction: column; align-items: center;
  }
  .brand__square {
    width: 110px; height: 110px;
    border: 2px solid var(--ink);
    margin-bottom: 34px;
  }
  .brand__name {
    font-family: "Cinzel", serif;
    font-weight: 400; font-size: 54px;
    letter-spacing: 0.12em; color: var(--ink);
    white-space: nowrap; line-height: 1.2;
  }
  .label__metal {
    position: absolute; left: 0; top: 673px; width: 1000px; height: 18px;
    background: linear-gradient(90deg, var(--silver-dark) 0%, var(--silver-light) 40%, var(--silver-dark) 60%, var(--silver-light) 85%, var(--silver-dark) 100%);
  }
  .varietal {
    position: absolute; left: 0; top: 691px; width: 1000px; height: 289px;
    background: var(--band-pink);
  }
  .varietal__gold-rule {
    position: absolute; left: 0; top: 44px; width: 1000px; height: 2px;
    background: linear-gradient(90deg, #8d6d3c, #e4c98f, #8d6d3c);
  }
  .varietal__name {
    position: absolute; left: 0; top: 68px; width: 1000px;
    text-align: center;
    font-family: "Allura", cursive;
    font-size: 120px; color: var(--ink); line-height: 1;
  }
  .origin {
    position: absolute; left: 0; top: 236px; width: 1000px;
    display: flex; align-items: center; justify-content: center; gap: 22px;
    font-family: "Cormorant Garamond", serif; font-weight: 500;
    font-size: 30px; letter-spacing: 0.04em; line-height: 1;
  }
  .origin__line { width: 130px; height: 2px; background: var(--gold); }
  .origin__region { color: var(--gold); }
  .origin__vintage { color: var(--ink); }
  .origin__divider { width: 1.5px; height: 40px; background: var(--ink); }
</style>
</head>
<body>
  <main class="label">
    <div class="label__field" role="img" aria-label="Soft pink topographic contour pattern across the label"></div>
    <div class="label__rule label__rule--top"></div>
    <div class="label__rule label__rule--bottom"></div>

    <div class="brand">
      <div class="brand__square"></div>
      <h1 class="brand__name">QUAILBROOK VINEYARDS</h1>
    </div>

    <div class="label__metal"></div>

    <section class="varietal">
      <div class="varietal__gold-rule"></div>
      <p class="varietal__name">Rose</p>
      <div class="origin">
        <span class="origin__line"></span>
        <span class="origin__region">PACIFIC</span>
        <span class="origin__divider"></span>
        <span class="origin__vintage">2025</span>
        <span class="origin__divider"></span>
        <span class="origin__region">NORTHWEST</span>
        <span class="origin__line"></span>
      </div>
    </section>
  </main>
</body>
</html>
```